New business card for a regional office of a US M&A company

We need business card for a finance company, office based in Hong Kong , our Head office is in US, our business is to Merge and acquires companies , the new office will be a regional office for the Asia Pacific region. We want to use the head office logo as attached ( but don't have to be exactly the same, can be a variation to it) as a base and then add Asia Pacific alongside the logo.
We would prefer to have be bilingual Eng + Chinese, although we don't really have Chinese company name .

Industry/Entity Type

Business

Contact Information for Business Card

Clara Jo Tsang
 

VP,
APAC M&A Operations
Orin Vantage Asia Pacific Limited
 
Unit 1407, K18
18 Tai Lok Shan Road, 
Hong Kong 
 
M: +852 6038 1742
T : +852 2836 4100
F : +852 2836 4177
VOIP: 4158
 
cjtsang@orinvantage.com

Font styles to use
Serif
Sans Serif

Colors

Designer to choose colors to be used in the design.

Requirements
Must have
• APAC Office

```html
<!DOCTYPE html>
<html lang="en">
<head>
<meta charset="utf-8">
<title>Orin Vantage – APAC Business Card</title>
<link rel="stylesheet" href="https://fonts.googleapis.com/css2?family=Roboto:wght@400;700&family=Roboto+Condensed:wght@700&display=swap">
<style>
  :root {
    --stage: #2b2b2b;
    --navy: #0f2842;
    --cyan: #21acd0;
    --white: #ffffff;
    --mist: #e9eef2;
    --ink-on-cyan: #0f2842;
    --text-on-cyan: #f1f7fa;
  }
  * { margin: 0; padding: 0; box-sizing: border-box; }
  html, body {
    width: 1200px; height: 960px; overflow: hidden;
    background: var(--stage);
    font-family: "Roboto", Arial, sans-serif;
  }
  .card {
    position: absolute;
    left: 320px;
    width: 600px;
    height: 342px;
    overflow: hidden;
  }

  /* Card back */
  .card-back { top: 105px; background: var(--navy); }
  .card-back .brand {
    position: absolute; top: 140px; left: 0; width: 100%;
    display: flex; justify-content: center; align-items: center; gap: 14px;
    color: var(--mist);
    font: 700 34px/1 "Roboto", Arial, sans-serif;
    letter-spacing: 2px;
  }
  .card-back .brand-square { width: 22px; height: 22px; background: var(--mist); }
  .card-back .website {
    position: absolute; top: 288px; left: 0; width: 100%;
    text-align: center; color: var(--mist);
    font-size: 14px; letter-spacing: 6px;
  }

  /* Card front */
  .card-front { top: 493px; background: var(--navy); }
  .card-front .split { position: absolute; inset: 0; }
  .card-front .brand {
    position: absolute; left: 0; top: 130px; width: 302px;
    display: flex; flex-direction: column; align-items: center; gap: 18px;
  }
  .card-front .brand-square { width: 40px; height: 40px; background: var(--mist); }
  .card-front .brand-name {
    color: var(--cyan);
    font: 700 33px/1 "Roboto", Arial, sans-serif;
  }
  .contact {
    position: absolute; right: 32px; top: 28px;
    text-align: right; color: var(--text-on-cyan);
    font-size: 14.5px; line-height: 19px;
  }
  .contact .name {
    font: 700 21px/1 "Roboto Condensed", "Arial Narrow", sans-serif;
    color: var(--ink-on-cyan);
  }
  .contact .title {
    font-size: 15px; color: var(--text-on-cyan); margin-top: 6px;
  }
  .contact .address { margin-top: 46px; }
  .contact .phones { margin-top: 8px; }
  .contact .phones li {
    list-style: none; display: flex; justify-content: flex-end; align-items: center; gap: 6px;
  }
  .contact .phones svg { width: 14px; height: 14px; fill: var(--ink-on-cyan); }
  .contact .voip { margin-top: 10px; }
</style>
</head>
<body>

<section class="card card-back" aria-label="Card back">
  <div class="brand"><span class="brand-square"></span><span>ORIN VANTAGE</span></div>
  <p class="website">www.orinvantage.com</p>
</section>

<section class="card card-front" aria-label="Card front">
  <svg class="split" width="600" height="342" viewBox="0 0 600 342" aria-hidden="true">
    <polygon points="304,0 600,0 600,342 304,342 304,60 313,50 304,40" fill="var(--cyan)"/>
    <polyline points="302,0 302,38 312,49 302,60 302,342" fill="none" stroke="var(--white)" stroke-width="3"/>
  </svg>

  <div class="brand">
    <span class="brand-square"></span>
    <span class="brand-name">ORIN VANTAGE</span>
  </div>

  <div class="contact">
    <h1 class="name">CLARA JO TSANG</h1>
    <p class="title">VP</p>
    <address class="address" style="font-style:normal">
      APAC M&amp;A Operations<br>
      Orin Vantage Asia Pacific Limited<br>
      Unit 1407, K18<br>
      18 Tai Lok Shan Road<br>
      Hong Kong
    </address>
    <ul class="phones">
      <li>+852 2836 4100
        <svg viewBox="0 0 24 24" aria-label="Telephone"><path d="M6.6 10.8a15 15 0 0 0 6.6 6.6l2.2-2.2a1 1 0 0 1 1-.25 11.4 11.4 0 0 0 3.6.57 1 1 0 0 1 1 1V20a1 1 0 0 1-1 1A17 17 0 0 1 3 4a1 1 0 0 1 1-1h3.5a1 1 0 0 1 1 1 11.4 11.4 0 0 0 .57 3.6 1 1 0 0 1-.25 1z"/></svg>
      </li>
      <li>+852 6038 1742
        <svg viewBox="0 0 24 24" aria-label="Mobile"><path d="M7 1h10a2 2 0 0 1 2 2v18a2 2 0 0 1-2 2H7a2 2 0 0 1-2-2V3a2 2 0 0 1 2-2zm0 3v14h10V4zm5 15.5a1 1 0 1 0 0 2 1 1 0 0 0 0-2z"/></svg>
      </li>
      <li>+852 2836 4177
        <svg viewBox="0 0 24 24" aria-label="Fax"><path d="M6 2h10l2 2v5H6zM3 10h18a2 2 0 0 1 2 2v8H1v-8a2 2 0 0 1 2-2zm3 6v6h12v-6z"/></svg>
      </li>
    </ul>
    <p class="voip">VOIP: 4158</p>
  </div>
</section>

</body>
</html>
```